New bussiness card, using company logo.
Lionel Brisk
Manager/Director
Brisk Property Developments
Po Box 5347
Ferncliff Central
Vale
0491 638 205
lionel@briskpropertydevelopments
eye catching, vibrant colours, professional

```html
<!DOCTYPE html>
<html lang="en">
<head>
<meta charset="utf-8">
<title>Lionel Brisk – Business Card</title>
<link rel="stylesheet" href="https://fonts.googleapis.com/css2?family=Source+Sans+3:wght@400;600;700&display=swap">
<style>
  :root {
    --card-bg: #ffffff;
    --name-blue: #3b8ae6;
    --ink: #1b1b1b;
    --rule-grey: #bdbdbd;
    --icon-grey: #7a7a7a;
    --brand-red: #e51f30;
    --band-red: #9b0a06;
    --band-red-deep: #8a0804;
    --lime: #8fd92a;
    --footer-ink: #1a0a08;
  }
  html, body {
    margin: 0;
    padding: 0;
    width: 1200px;
    height: 667px;
    overflow: hidden;
    background: var(--card-bg);
  }
  .card {
    position: relative;
    width: 1200px;
    height: 667px;
    background: var(--card-bg);
    font-family: "Source Sans 3", "Myriad Pro", Arial, sans-serif;
    color: var(--ink);
    overflow: hidden;
  }
  .footer-band {
    position: absolute;
    left: 0;
    right: 0;
    top: 530px;
    bottom: 0;
    background: linear-gradient(180deg, var(--band-red) 0%, var(--band-red-deep) 100%);
  }
  .brand {
    position: absolute;
    left: 60px;
    top: 238px;
    width: 540px;
    display: flex;
    align-items: center;
    gap: 22px;
  }
  .brand-mark {
    flex: none;
    width: 34px;
    height: 34px;
    background: var(--lime);
  }
  .brand-name {
    margin: 0;
    font-size: 50px;
    line-height: 1.05;
    font-weight: 700;
    color: var(--brand-red);
  }
  .identity {
    position: absolute;
    left: 641px;
    top: 72px;
  }
  .person-name {
    margin: 0;
    font-size: 56px;
    font-weight: 400;
    line-height: 1;
    color: var(--name-blue);
  }
  .person-role {
    margin: 16px 0 0;
    font-size: 38px;
    font-weight: 400;
    line-height: 1;
    color: var(--ink);
  }
  .rule {
    position: absolute;
    left: 629px;
    right: 0;
    top: 208px;
    height: 0;
    border-top: 1.5px solid var(--rule-grey);
  }
  .contacts {
    position: absolute;
    left: 624px;
    top: 266px;
    margin: 0;
    padding: 0;
    list-style: none;
    font-size: 29px;
    line-height: 1.15;
  }
  .contact {
    display: flex;
    align-items: flex-start;
    gap: 10px;
    margin-bottom: 10px;
  }
  .contact-icon {
    flex: none;
    width: 36px;
    height: 32px;
    margin-top: 2px;
  }
  .contact-phone { margin-top: 4px; }
  .footer-name {
    position: absolute;
    right: 44px;
    top: 588px;
    margin: 0;
    font-size: 36px;
    font-weight: 700;
    color: var(--footer-ink);
  }
</style>
</head>
<body>
<div class="card">
  <div class="footer-band" role="img" aria-label="Decorative red and lime wave band along the bottom of the card"></div>

  <div class="brand">
    <span class="brand-mark"></span>
    <p class="brand-name">Brisk Property Developments</p>
  </div>

  <div class="identity">
    <h1 class="person-name">Lionel Brisk</h1>
    <p class="person-role">Manager/Director</p>
  </div>
  <div class="rule"></div>

  <ul class="contacts">
    <li class="contact">
      <svg class="contact-icon" viewBox="0 0 36 32" aria-hidden="true">
        <rect x="3" y="8" width="30" height="18" fill="var(--icon-grey)"/>
        <path d="M3,8 L18,19 L33,8" fill="none" stroke="#ffffff" stroke-width="2"/>
      </svg>
      <span>Po Box 5347</span>
    </li>
    <li class="contact">
      <svg class="contact-icon" viewBox="0 0 36 32" aria-hidden="true">
        <path d="M18,2 C11,2 7,7 7,12 C7,19 18,31 18,31 C18,31 29,19 29,12 C29,7 25,2 18,2 Z" fill="var(--icon-grey)"/>
        <circle cx="18" cy="12" r="3.5" fill="var(--brand-red)"/>
      </svg>
      <span>Ferncliff Central<br>Vale</span>
    </li>
    <li class="contact">
      <svg class="contact-icon contact-phone" viewBox="0 0 36 32" aria-hidden="true">
        <path d="M3,10 C3,4 33,4 33,10 L33,13 L26,13 L26,9 L10,9 L10,13 L3,13 Z" fill="var(--icon-grey)"/>
        <rect x="8" y="14" width="20" height="15" rx="3" fill="var(--icon-grey)"/>
        <g fill="#ffffff">
          <circle cx="13" cy="18" r="1.4"/><circle cx="18" cy="18" r="1.4"/><circle cx="23" cy="18" r="1.4"/>
          <circle cx="13" cy="22" r="1.4"/><circle cx="18" cy="22" r="1.4"/><circle cx="23" cy="22" r="1.4"/>
          <circle cx="13" cy="26" r="1.4"/><circle cx="18" cy="26" r="1.4"/><circle cx="23" cy="26" r="1.4"/>
        </g>
      </svg>
      <span>0491 638 205</span>
    </li>
    <li class="contact">
      <svg class="contact-icon" viewBox="0 0 36 32" aria-hidden="true">
        <circle cx="18" cy="17" r="13" fill="none" stroke="var(--icon-grey)" stroke-width="2.5"/>
        <circle cx="18" cy="17" r="5" fill="none" stroke="var(--icon-grey)" stroke-width="2.5"/>
        <path d="M23,12 L23,20 C23,24 30,24 30,17" fill="none" stroke="var(--icon-grey)" stroke-width="2.5"/>
      </svg>
      <span>lionel@briskpropertydevelopments</span>
    </li>
  </ul>

  <p class="footer-name">Brisk Property Developments</p>
</div>
</body>
</html>
```